Modern looking signage for dental office.

Exterior signage for passing cars
Updates
Need extra days to review
Target Market(s)
Cars passing by
Font styles to use
Sans Serif
Colors
3276b5
Requirements
Must have
- Logo
- OPEN ON SUTURDAY AND SUNDAY
- NIGHT CLINIC AVAILABLE
- PLEASE USE THE FONT TYPE IN FILE 4 UPLOADED BELOW.
- (847) 302-7469
- Modern looking

```html
<!DOCTYPE html>
<html lang="en">
<head>
<meta charset="UTF-8">
<title>Nova Dental – Exterior Sign</title>
<link href="https://fonts.googleapis.com/css2?family=Arimo:wght@700&family=Josefin+Sans:wght@300;400&display=swap" rel="stylesheet">
<style>
  :root {
    --brand-blue: #1a5fa8;
    --ink: #2f2b2a;
    --panel: #ffffff;
    --backdrop: #e9eaec;
    --edge: #c9ccd1;
  }
  * { margin: 0; padding: 0; box-sizing: border-box; }
  html, body { width: 1200px; height: 1200px; overflow: hidden; }
  body { background: var(--backdrop); position: relative; }

  .sign-main, .sign-strip {
    position: absolute;
    left: 100px;
    width: 1000px;
    background: var(--panel);
    overflow: hidden;
    box-shadow: 0 0 0 1px var(--edge);
  }
  .sign-main { top: 200px; height: 560px; }
  .sign-strip { top: 820px; height: 170px; }

  .brand {
    position: absolute;
    left: 70px;
    top: 70px;
    display: flex;
    align-items: center;
    gap: 30px;
  }
  .brand-circle {
    width: 150px;
    height: 150px;
    border: 3px solid var(--ink);
    border-radius: 50%;
    flex: none;
  }
  .brand-text { display: flex; flex-direction: column; white-space: nowrap; }
  .brand-name {
    font-family: "Josefin Sans", sans-serif;
    font-weight: 400;
    font-size: 84px;
    line-height: 1;
    color: var(--ink);
    letter-spacing: 2px;
  }
  .brand-tagline {
    font-family: "Josefin Sans", sans-serif;
    font-weight: 400;
    font-size: 30px;
    line-height: 1;
    color: var(--ink);
    letter-spacing: 1px;
    margin-top: 14px;
    padding-left: 50px;
  }

  .night-band {
    position: absolute;
    left: 300px;
    top: 290px;
    width: 700px;
    height: 270px;
    background: var(--brand-blue);
    clip-path: polygon(0 0, 100% 0, 100% 100%, 15% 100%);
  }
  .night-text {
    position: absolute;
    left: 470px;
    top: 320px;
    font-family: "Arimo", sans-serif;
    font-weight: 700;
    font-size: 72px;
    line-height: 1.18;
    color: #fff;
    white-space: nowrap;
  }

  .phone {
    position: absolute;
    left: 40px;
    top: 0;
    height: 170px;
    display: flex;
    align-items: center;
    font-family: "Arimo", sans-serif;
    font-weight: 700;
    font-size: 56px;
    color: #111;
    white-space: nowrap;
  }
  .weekend-band {
    position: absolute;
    left: 500px;
    top: 0;
    width: 500px;
    height: 170px;
    background: var(--brand-blue);
    clip-path: polygon(0 0, 100% 0, 100% 100%, 14% 100%);
  }
  .weekend-text {
    position: absolute;
    left: 585px;
    top: 0;
    height: 170px;
    display: flex;
    flex-direction: column;
    justify-content: center;
    font-family: "Arimo", sans-serif;
    font-weight: 700;
    font-size: 38px;
    line-height: 1.2;
    color: #fff;
    white-space: nowrap;
  }
</style>
</head>
<body>
  <section class="sign-main">
    <div class="brand">
      <div class="brand-circle"></div>
      <div class="brand-text">
        <span class="brand-name">NOVA DENTAL</span>
        <span class="brand-tagline">MODERN GENERAL DENTISTRY</span>
      </div>
    </div>
    <div class="night-band"></div>
    <p class="night-text">Night Clinic<br>Available</p>
  </section>

  <section class="sign-strip">
    <p class="phone">(847) 302-7469</p>
    <div class="weekend-band"></div>
    <p class="weekend-text"><span>Open on</span><span>Saturday and Sunday</span></p>
  </section>
</body>
</html>
```